CrumbSteward Retail box packaging- 25cm x 10cm x10cm

Retail Packaging. For: Natural Peanut Butter Electric Mixer.<br/>THE CRUMB STEWARD- the natural peanut butter mixer.<br/>25cm x 10 x10. Full colour . White , cobalt grey and turquoise or green accents.<br/>Product description:<br/>New mixer customized for mixing in store bought natural nut butters that naturally separate on the shelf.—- oil above and nuts below. <br/>Making.the messy mix-in an absolute breeze! <br/>3 speed high torque custom motor. With unique 2mm Stainless Steel hook designed to draw oil down and force nuts up into the vortex...without displacing the oil and mixing it perfectly from top to bottom. Quick release buttons and dishwasher safe<br/>No Mess-No Waste -Better Taste<br/>Mix once at room temperature then refrigerate and Done.<br/>Would love to include graphics showing all nuts with leaves to show it’s perfect for all types of nut butters.<br/>Peanut- Almond-Cashew- Macadamia- Hazelnut- Pistachio<br/><br/>I am waiting for final prototype photography. Currently working with CAD drawings. But want to get packaging going. <br/>Mixer will be black with a Stainless Steel not the gold/black as shown. We will drop in product photo later.<br/>Right side of box should be for healthy colourful peanut butter snack images. Ie red apples and peanut butter. I saw some beautiful stock photo images. Will pay for those images above sketch swarm cost. <br/>I will also upload a high res design file of my logo.<br/><br/>I am happy to provide a word document with all necessary text. Or you can work with the above text and I’ll add or tweak text as needed, once the look is established. Please let me know your preference.<br/><br/>

Target Market(s)

North American (Canadian and US) moms. Needs to look high quality. German style quality and image. Like Velka and Dorminex, Tavelorno,

Colors
0692cd
afd34e

Requirements
Must have
• Adding Oily jar of peanut butter on front of box with mixer lowering into jar. Please cover or hide any brand names.

```html
<!DOCTYPE html>
<html lang="en">
<head>
<meta charset="utf-8">
<title>CrumbSteward – Natural Peanut Butter Mixer Packaging</title>
<link rel="stylesheet" href="https://fonts.googleapis.com/css2?family=Audiowide&family=Roboto+Slab:wght@400;600&display=swap">
<style>
  :root{
    --bg:#d9dadb;
    --paper:#f2f4f5;
    --teal:#3b8e8d;
    --slate:#3f3c52;
    --ink:#2f3147;
    --display:"Audiowide", sans-serif;
    --body:"Roboto Slab", serif;
  }
  *{box-sizing:border-box;margin:0;padding:0}
  html,body{width:1200px;height:1200px;overflow:hidden;background:var(--bg)}
  .sheet{position:relative;width:1200px;height:1200px}
  .panel{position:absolute;background:var(--paper);overflow:hidden;box-shadow:0 2px 6px rgba(0,0,0,.12)}
  .brand{font-family:var(--display);letter-spacing:.5px;display:flex;align-items:center;gap:8px;white-space:nowrap}
  .brand__mark{width:14px;height:14px;background:currentColor;display:inline-block}
  .brand__sub{font-family:var(--display);font-size:8px;letter-spacing:1px;white-space:nowrap}
  .placeholder{position:absolute;border-radius:6px}

  /* top panel */
  .top-panel{left:60px;top:60px;width:750px;height:300px;background:var(--teal)}
  .top-panel .brand{position:absolute;left:0;right:0;top:95px;justify-content:center;color:var(--slate);font-size:44px}
  .top-panel .top-title{position:absolute;left:0;right:0;top:170px;text-align:center;font-family:var(--display);font-size:30px;color:var(--slate)}

  /* front panel */
  .front-panel{left:60px;top:450px;width:750px;height:300px}
  .front-band{position:absolute;left:0;top:0;width:750px;height:14px;background:var(--teal)}
  .front-side{position:absolute;left:20px;top:14px;width:230px;height:286px;background:var(--slate)}
  .front-side .brand{position:absolute;left:0;right:0;top:34px;justify-content:center;color:var(--teal);font-size:18px}
  .front-side .rule{position:absolute;left:18px;right:18px;top:86px;height:1px;background:#8a889a}
  .front-title{position:absolute;left:0;right:0;top:102px;text-align:center;font-family:var(--display);font-weight:400;font-size:19px;line-height:1.25;color:#fff}
  .jar{left:0;top:180px;width:250px;height:120px;border-radius:0 60px 0 0;background:radial-gradient(ellipse at 40% 40%,#9a6a44,#6f4a2f)}
  .mixer-front{left:350px;top:26px;width:300px;height:150px;border-radius:80px 30px 80px 30px;background:linear-gradient(135deg,#5a5a5a,#1e1e1e 55%,#b9bcbf)}
  .hook-area{left:255px;top:150px;width:110px;height:70px;border-radius:8px;background:linear-gradient(135deg,#c9cbcd,#a6835f)}
  .front-tagline{position:absolute;left:370px;top:185px;font-family:var(--display);font-size:17px;color:var(--ink);white-space:nowrap}
  .nuts{position:absolute;left:368px;top:224px;display:flex;gap:9px}
  .nut{width:50px;text-align:center}
  .nut__pic{width:50px;height:50px;border-radius:50%;background:var(--slate);position:relative}
  .nut__pic::after{content:"";position:absolute;inset:12px;border-radius:50%}
  .nut--peanut .nut__pic::after{background:#d9b071}
  .nut--almond .nut__pic::after{background:#c07a3e}
  .nut--cashew .nut__pic::after{background:#e2c99a}
  .nut--macadamia .nut__pic::after{background:#8fbf4e}
  .nut--hazelnut .nut__pic::after{background:#9b6a3d}
  .nut--pistachio .nut__pic::after{background:#a9c56a}
  .nut__label{font-family:var(--body);font-weight:600;font-size:7px;color:var(--teal);margin-top:6px;letter-spacing:.3px}

  /* right side panel */
  .side-panel{left:840px;top:450px;width:300px;height:300px}
  .snack-photo{position:absolute;inset:0;background:linear-gradient(135deg,#b7402f,#d46a43 45%,#6b4a35)}
  .side-panel .brand{position:absolute;left:0;right:0;top:52px;justify-content:center;color:#fff;font-size:20px}

  /* back panel */
  .back-panel{left:60px;top:840px;width:750px;height:300px}
  .back-panel .brand{position:absolute;left:30px;top:70px;color:var(--slate);font-size:22px}
  .back-panel .brand__sub{position:absolute;left:30px;top:104px;color:var(--slate)}
  .back-panel .rule{position:absolute;left:30px;top:122px;width:150px;height:2px;background:var(--teal)}
  .back-tagline{position:absolute;left:30px;top:140px;font-family:var(--body);font-size:11px;color:var(--ink)}
  .mixer-back{left:300px;top:40px;width:260px;height:130px;border-radius:70px 20px 70px 20px;background:linear-gradient(160deg,#1d1d1d,#9ea2a6 50%,#111)}
  .note{position:absolute;left:30px;top:240px;padding-left:8px;border-left:2px solid var(--teal);font-family:var(--body);font-size:9px;line-height:1.35;color:var(--ink)}
  .features{position:absolute;left:390px;top:205px;display:flex;gap:22px}
  .feature{width:80px;text-align:center;font-family:var(--body);font-weight:600;font-size:9px;line-height:1.25;color:var(--ink)}
  .feature svg{display:block;margin:0 auto 8px}

  /* back side panel */
  .end-panel{left:840px;top:840px;width:300px;height:300px}
  .end-head{position:absolute;left:0;top:0;width:300px;height:120px;background:var(--teal)}
  .end-head .brand{position:absolute;left:80px;top:52px;color:var(--slate);font-size:17px}
  .end-head .brand__sub{position:absolute;left:80px;top:78px;color:var(--slate);font-size:6px}
  .mixer-upright{left:22px;top:30px;width:40px;height:200px;border-radius:20px 20px 14px 14px;background:linear-gradient(90deg,#1a1a1a,#b8bbbe 50%,#1a1a1a)}
  .end-tagline{position:absolute;left:80px;top:135px;font-family:var(--body);font-size:8px;color:var(--ink)}
  .end-copy{position:absolute;left:80px;top:158px;width:200px;font-family:var(--body);font-size:7px;line-height:1.4;color:var(--ink)}
  .end-nuts{position:absolute;left:80px;top:250px;display:flex;gap:5px}
  .end-nuts span{width:22px;height:22px;border-radius:50%;background:var(--slate)}
</style>
</head>
<body>
<main class="sheet">

  <section class="panel top-panel" aria-label="Top panel">
    <div class="brand"><span class="brand__mark"></span>CrumbSteward</div>
    <div class="top-title">Natural Peanut Butter Mixer</div>
  </section>

  <section class="panel front-panel" aria-label="Front panel">
    <div class="front-band"></div>
    <div class="front-side">
      <div class="brand"><span class="brand__mark"></span>CrumbSteward</div>
      <div class="rule"></div>
      <h1 class="front-title">Natural Peanut<br>Butter Mixer</h1>
    </div>
    <div class="placeholder jar" role="img" aria-label="Glass jar of oily natural peanut butter"></div>
    <div class="placeholder mixer-front" role="img" aria-label="Black and stainless steel electric mixer with red buttons"></div>
    <div class="placeholder hook-area" role="img" aria-label="Stainless steel mixing hook lowering into the jar"></div>
    <p class="front-tagline">No Mess-No Waste-Better Taste</p>
    <div class="nuts">
      <div class="nut nut--peanut"><div class="nut__pic" role="img" aria-label="Peanuts with leaves"></div><div class="nut__label">PEANUT</div></div>
      <div class="nut nut--almond"><div class="nut__pic" role="img" aria-label="Almonds with leaves"></div><div class="nut__label">ALMOND</div></div>
      <div class="nut nut--cashew"><div class="nut__pic" role="img" aria-label="Cashews with leaves"></div><div class="nut__label">CASHEW</div></div>
      <div class="nut nut--macadamia"><div class="nut__pic" role="img" aria-label="Macadamia nuts with leaves"></div><div class="nut__label">MACADAMIA</div></div>
      <div class="nut nut--hazelnut"><div class="nut__pic" role="img" aria-label="Hazelnuts with leaves"></div><div class="nut__label">HAZELNUT</div></div>
      <div class="nut nut--pistachio"><div class="nut__pic" role="img" aria-label="Pistachios with leaves"></div><div class="nut__label">PISTACHIO</div></div>
    </div>
  </section>

  <section class="panel side-panel" aria-label="Right side panel">
    <div class="snack-photo" role="img" aria-label="Sliced red apples with peanut butter on a wooden board"></div>
    <div class="brand"><span class="brand__mark"></span>CrumbSteward</div>
  </section>

  <section class="panel back-panel" aria-label="Back panel">
    <div class="brand"><span class="brand__mark"></span>CrumbSteward</div>
    <div class="brand__sub">THE NATURAL PEANUT BUTTER MIXER</div>
    <div class="rule"></div>
    <p class="back-tagline">No Mess-No Waste-Better Taste</p>
    <div class="placeholder mixer-back" role="img" aria-label="Electric mixer shown from the side"></div>
    <p class="note">Mix once at room temperature<br>then refrigerate and Done.</p>
    <div class="features">
      <div class="feature">
        <svg width="36" height="36" viewBox="0 0 36 36" aria-hidden="true"><circle cx="18" cy="18" r="15" fill="none" stroke="#3b8e8d" stroke-width="2"/><path d="M18 18 L18 8" stroke="#3b8e8d" stroke-width="2"/><circle cx="18" cy="18" r="2.5" fill="#3b8e8d"/></svg>
        3 speed high torque custom motor
      </div>
      <div class="feature">
        <svg width="36" height="36" viewBox="0 0 36 36" aria-hidden="true"><rect x="7" y="3" width="22" height="30" rx="2" fill="none" stroke="#3b8e8d" stroke-width="2"/><line x1="7" y1="10" x2="29" y2="10" stroke="#3b8e8d" stroke-width="2"/><circle cx="18" cy="21" r="6" fill="none" stroke="#3b8e8d" stroke-width="2"/></svg>
        Dishwasher safe
      </div>
      <div class="feature">
        <svg width="36" height="36" viewBox="0 0 36 36" aria-hidden="true"><circle cx="18" cy="18" r="15" fill="none" stroke="#3b8e8d" stroke-width="2"/><circle cx="18" cy="18" r="6" fill="#3b8e8d"/></svg>
        Quick release buttons
      </div>
    </div>
  </section>

  <section class="panel end-panel" aria-label="Back side panel">
    <div class="end-head">
      <div class="brand"><span class="brand__mark"></span>CrumbSteward</div>
      <div class="brand__sub">THE NATURAL PEANUT BUTTER MIXER</div>
    </div>
    <div class="placeholder mixer-upright" role="img" aria-label="Mixer standing upright with stainless steel hook"></div>
    <p class="end-tagline">No Mess-No Waste-Better Taste</p>
    <p class="end-copy">With unique 2mm Stainless Steel hook designed to draw oil down and force nuts up into the vortex, without displacing the oil and mixing it perfectly from top to bottom.</p>
    <div class="end-nuts" aria-hidden="true"><span></span><span></span><span></span><span></span><span></span><span></span></div>
  </section>

</main>
</body>
</html>
```